Birchline Septic Solutions

Would like to see some single sided ones but would also like to see some double sided with one sided only being the logo. Owners name is Colin Vandro. Phone number is 555-214-0387
Services are pumping, inspections, installs, and repairs

Contact Information for Business Card

555-241-0387 Colin Vandro Maple Hollow, OH

```html
<!DOCTYPE html>
<html lang="en">
<head>
<meta charset="utf-8">
<title>Birchline Septic Solutions – Business Cards</title>
<link rel="stylesheet" href="https://fonts.googleapis.com/css2?family=Jost:wght@400;500;700&family=Tinos:wght@400&display=swap">
<style>
  :root {
    --ink: #0b0b0b;
    --paper: #f4f4f4;
    --teal: #2bb5ad;
    --grey: #555555;
    --backdrop: #6b6b6b;
  }
  * { box-sizing: border-box; margin: 0; padding: 0; }
  html, body { width: 1200px; height: 900px; overflow: hidden; }
  body {
    background: var(--backdrop);
    font-family: "Jost", sans-serif;
    position: relative;
  }
  .card {
    position: absolute;
    width: 560px;
    height: 320px;
    overflow: hidden;
    background: var(--paper);
    box-shadow: 0 14px 30px rgba(0,0,0,.35);
  }
  .card-front { left: 90px; top: 100px; }
  .card-back { left: 550px; top: 480px; }
  .card svg.shape { position: absolute; inset: 0; }

  .wordmark {
    position: absolute;
    font-family: "Jost", sans-serif;
    font-weight: 700;
    line-height: 1;
    display: flex;
    align-items: center;
    gap: 12px;
  }
  .wordmark-square { width: 16px; height: 16px; background: currentColor; flex: none; }
  .wordmark-text { display: flex; flex-direction: column; }
  .wordmark-name { font-size: 46px; letter-spacing: 1px; }
  .wordmark-tag { font-size: 14px; letter-spacing: 5px; margin-top: 6px; }

  .card-front .wordmark { right: 34px; top: 62px; color: #ffffff; }
  .card-back .wordmark { left: 34px; top: 48px; color: var(--ink); }

  .owner { position: absolute; right: 40px; top: 34px; text-align: right; }
  .owner-role { font-size: 14px; color: var(--grey); }
  .owner-name { font-family: "Tinos", serif; font-size: 22px; color: var(--teal); letter-spacing: .5px; }

  .contact { position: absolute; left: 54px; top: 168px; list-style: none; }
  .contact li { display: flex; align-items: center; gap: 8px; font-size: 16px; color: var(--grey); margin-bottom: 6px; }
  .contact svg { width: 16px; height: 16px; fill: var(--teal); }

  .services-title {
    position: absolute; left: 54px; top: 236px;
    font-size: 17px; font-weight: 500; color: var(--teal);
  }
  .services-list {
    position: absolute; left: 20px; bottom: 10px;
    font-size: 16px; color: #ffffff;
  }
</style>
</head>
<body>

<!-- Front side: brand only -->
<section class="card card-front" aria-label="Card front">
  <svg class="shape" width="560" height="320" viewBox="0 0 560 320">
    <defs>
      <linearGradient id="ridgeFront" x1="0" y1="0" x2="0" y2="1">
        <stop offset="0" stop-color="#0b0b0b"/>
        <stop offset="1" stop-color="#d8d8d8"/>
      </linearGradient>
    </defs>
    <polygon points="0,0 560,0 560,170 300,215 0,250" fill="var(--ink)"/>
    <rect x="110" y="190" width="230" height="90" fill="url(#ridgeFront)" role="img" aria-label="Silhouette of mountain peaks and pine trees"/>
  </svg>
  <div class="wordmark">
    <span class="wordmark-square"></span>
    <span class="wordmark-text">
      <span class="wordmark-name">BIRCHLINE</span>
      <span class="wordmark-tag">SEPTIC SOLUTIONS</span>
    </span>
  </div>
</section>

<!-- Back side: contact details -->
<section class="card card-back" aria-label="Card back">
  <svg class="shape" width="560" height="320" viewBox="0 0 560 320">
    <defs>
      <linearGradient id="ridgeBack" x1="0" y1="0" x2="0" y2="1">
        <stop offset="0" stop-color="#e6e6e6"/>
        <stop offset="1" stop-color="#0b0b0b"/>
      </linearGradient>
    </defs>
    <polygon points="0,285 370,235 560,180 560,320 0,320" fill="var(--ink)"/>
    <rect x="370" y="120" width="190" height="120" fill="url(#ridgeBack)" role="img" aria-label="Silhouette of mountain peaks and pine trees"/>
  </svg>

  <div class="wordmark">
    <span class="wordmark-square"></span>
    <span class="wordmark-text">
      <span class="wordmark-name">BIRCHLINE</span>
      <span class="wordmark-tag">SEPTIC SOLUTIONS</span>
    </span>
  </div>

  <div class="owner">
    <p class="owner-role">Owners</p>
    <p class="owner-name">COLIN VANDRO</p>
  </div>

  <ul class="contact">
    <li>
      <svg viewBox="0 0 24 24" aria-hidden="true"><path d="M6.6 10.8a15 15 0 0 0 6.6 6.6l2.2-2.2a1 1 0 0 1 1-.25 11.4 11.4 0 0 0 3.6.57 1 1 0 0 1 1 1V20a1 1 0 0 1-1 1A17 17 0 0 1 3 4a1 1 0 0 1 1-1h3.5a1 1 0 0 1 1 1c0 1.25.2 2.45.57 3.6a1 1 0 0 1-.25 1z"/></svg>
      555-241-0387
    </li>
    <li>
      <svg viewBox="0 0 24 24" aria-hidden="true"><path d="M12 2a7 7 0 0 0-7 7c0 5.2 7 13 7 13s7-7.8 7-13a7 7 0 0 0-7-7zm0 9.5A2.5 2.5 0 1 1 12 6.5a2.5 2.5 0 0 1 0 5z"/></svg>
      Maple Hollow, OH
    </li>
  </ul>

  <p class="services-title">Our Services</p>
  <p class="services-list">Pumping, Inspections, Installs, And Repairs</p>
</section>

</body>
</html>
```